Need Help having my business card stand out

I am the owner of Birchway Canine Training and would like for my business cards to stand out. I have been trying to keep designing them myself but I can't get what I have in my head on the card. I will try my best to post templates that I like for inspirations. I want something unique but elegant. I don't want in to look cartoony or cheesy. It needs to pop in a pet shop but also in a coffee shop or gym.

Target Market(s)

Dog owners, Married ,No young kids Jr High school kids and up (maybe kids on the way) Executives, Stay at home moms/wives, Small business owners

Industry/Entity Type

Dog Training

Contact Information for Business Card

Lowell Spratt, 281-904-3376, info@birchwaycanine.example, www.birchwaycanine.example

Colors

Designer to choose colors to be used in the design.

Requirements
Must have
• my logo
Should not have
• Cursive lettering

```html
<!DOCTYPE html>
<html lang="en">
<head>
<meta charset="utf-8">
<title>Birchway Canine Training – Business Card</title>
<link href="https://fonts.googleapis.com/css2?family=Lato:wght@400;700&display=swap" rel="stylesheet">
<style>
  :root {
    --page-bg: #d6d6d4;
    --card-black: #060606;
    --card-charcoal: #2b2b2b;
    --text-light: #e4e2dc;
    --text-soft: #cfcdc7;
    --rule: #5a5a5a;
    --icon-box: #2e2e2e;
    --icon-ink: #6f6f6f;
    --ring: #1d1d1d;
    --photo-light: #8a8468;
    --photo-mid: #4b4a3e;
    --photo-dark: #1f1f26;
  }
  html, body {
    margin: 0;
    width: 1200px;
    height: 1200px;
    overflow: hidden;
    background: var(--page-bg);
  }
  .canvas {
    width: 1200px;
    height: 1200px;
    display: flex;
    align-items: center;
    justify-content: center;
  }
  .business-card {
    position: relative;
    width: 1000px;
    height: 598px;
    overflow: hidden;
    background:
      radial-gradient(ellipse 520px 380px at 480px 560px, rgba(255,255,255,0.12), transparent 70%),
      linear-gradient(180deg, var(--card-black) 0%, #121212 55%, var(--card-charcoal) 100%);
    box-shadow: 0 10px 30px rgba(0,0,0,0.25);
    font-family: "Lato", sans-serif;
  }
  .photo-panel {
    position: absolute;
    inset: 0;
  }
  .brand-block {
    position: absolute;
    left: 60px;
    top: 96px;
    width: 250px;
    display: flex;
    align-items: center;
    gap: 14px;
  }
  .brand-dot {
    flex: 0 0 18px;
    height: 18px;
    border-radius: 50%;
    background: var(--text-light);
  }
  .brand-name {
    margin: 0;
    color: var(--text-light);
    font-weight: 700;
    font-size: 30px;
    line-height: 1.15;
  }
  .contact-list {
    position: absolute;
    left: 58px;
    top: 282px;
    margin: 0;
    padding: 0;
    list-style: none;
  }
  .contact-item {
    position: absolute;
    left: 0;
    display: flex;
    align-items: center;
    gap: 14px;
    color: var(--text-soft);
    font-size: 25px;
    white-space: nowrap;
  }
  .contact-item.phone { top: 0; }
  .contact-item.email { top: 80px; }
  .contact-item.web { top: 123px; }
  .contact-icon {
    width: 22px;
    height: 22px;
    background: var(--icon-box);
    border-radius: 2px;
    display: flex;
    align-items: center;
    justify-content: center;
  }
  .contact-icon svg { width: 14px; height: 14px; }
  .name-row {
    position: absolute;
    left: 0;
    top: 494px;
    width: 570px;
    display: flex;
    align-items: center;
    gap: 20px;
  }
  .name-rule {
    height: 1px;
    background: var(--rule);
    flex: 1;
  }
  .name-rule.leading { flex: 0 0 146px; }
  .owner-name {
    margin: 0;
    color: var(--text-light);
    font-size: 31px;
    font-weight: 400;
    letter-spacing: 0.5px;
  }
</style>
</head>
<body>
<main class="canvas">
  <section class="business-card">
    <svg class="photo-panel" viewBox="0 0 1000 598" width="1000" height="598">
      <defs>
        <linearGradient id="photoTone" x1="0" y1="0" x2="0.3" y2="1">
          <stop offset="0" stop-color="var(--photo-light)"/>
          <stop offset="0.45" stop-color="var(--photo-mid)"/>
          <stop offset="1" stop-color="var(--photo-dark)"/>
        </linearGradient>
      </defs>
      <path d="M604,0 C520,90 470,420 655,598 L1000,598 L1000,0 Z"
            fill="url(#photoTone)" role="img"
            aria-label="Photo of the trainer kneeling outdoors beside a shepherd dog"/>
      <path d="M604,0 C520,90 470,420 655,598" fill="none" stroke="var(--ring)" stroke-width="14"/>
    </svg>

    <div class="brand-block">
      <span class="brand-dot"></span>
      <p class="brand-name">Birchway Canine Training</p>
    </div>

    <ul class="contact-list">
      <li class="contact-item phone">
        <span class="contact-icon">
          <svg viewBox="0 0 24 24"><path fill="var(--icon-ink)" d="M6.6 10.8a15.1 15.1 0 0 0 6.6 6.6l2.2-2.2c.3-.3.7-.4 1-.2 1.1.4 2.3.6 3.6.6.6 0 1 .4 1 1V20c0 .6-.4 1-1 1A17 17 0 0 1 3 4c0-.6.4-1 1-1h3.5c.6 0 1 .4 1 1 0 1.3.2 2.5.6 3.6.1.3 0 .7-.2 1z"/></svg>
        </span>
        281-904-3376
      </li>
      <li class="contact-item email">
        <span class="contact-icon">
          <svg viewBox="0 0 24 24"><path fill="var(--icon-ink)" d="M3 5h18v14H3z"/><path fill="none" stroke="var(--icon-box)" stroke-width="2" d="M3 6l9 7 9-7"/></svg>
        </span>
        info@birchwaycanine.example
      </li>
      <li class="contact-item web">
        <span class="contact-icon">
          <svg viewBox="0 0 24 24"><circle cx="12" cy="12" r="9" fill="none" stroke="var(--icon-ink)" stroke-width="2.5"/><path fill="none" stroke="var(--icon-ink)" stroke-width="2" d="M3 12h18M12 3c3 3 3 15 0 18M12 3c-3 3-3 15 0 18"/></svg>
        </span>
        www.birchwaycanine.example
      </li>
    </ul>

    <div class="name-row">
      <span class="name-rule leading"></span>
      <h1 class="owner-name">LOWELL SPRATT</h1>
      <span class="name-rule"></span>
    </div>
  </section>
</main>
</body>
</html>
```